Finiding oppertunites in Real Estate 6.15.20

size of ad 7” x 9.6”
1-I like the ad to stand out and attract people's attention.
2-you should be able to see the text of the ad clearly .. see the attachment anything in yellow is instructions.
3-the list of topics should not be the main part of the ad
4-if you decide you want a picture or vector of a person .. (you decide)
then it should be a white male about 25-30 years old wearing a solid white or blue shirt and not long hair.
5-leave 1 inch for footer
see attachment
Good luck

Target Market(s)

potential male students 25-35 years of age

Industry/Entity Type

Education

Requirements
Must have
• will stand out and people would want to see it.
should be able to read the words of ad
Nice to have
• how to make money in real estate on one line

```html
<!DOCTYPE html>
<html lang="en">
<head>
<meta charset="utf-8">
<title>Real Estate Career Course</title>
<link rel="stylesheet" href="https://fonts.googleapis.com/css2?family=Oswald:wght@300;400;500;700&family=Montserrat:wght@800&display=swap">
<style>
  :root {
    --navy-mid: #27466f;
    --navy-dark: #0f1f42;
    --title-blue: #1f3b66;
    --accent-blue: #2f5c9c;
    --paper: #f4f4f4;
    --footer-grey: #dcdcdc;
    --topic-ink: #3d4b63;
    --white: #ffffff;
  }
  * { margin: 0; padding: 0; box-sizing: border-box; }
  html, body { width: 875px; height: 1200px; overflow: hidden; background: var(--paper); }
  .flyer {
    position: relative; width: 875px; height: 1200px; overflow: hidden;
    font-family: "Oswald", "Arial Narrow", sans-serif; background: var(--paper);
  }
  .backdrop { position: absolute; inset: 0; }

  .headline {
    position: absolute; top: 38px; left: 495px; width: 300px; text-align: center;
    font-weight: 700; font-size: 50px; line-height: 48px; color: var(--title-blue);
    white-space: nowrap; transform: scaleX(0.86); transform-origin: center top;
  }

  .pitch { position: absolute; inset: 0; pointer-events: none; }
  .pitch-line {
    position: absolute; left: 91px; white-space: nowrap; color: var(--white);
    font-size: 36px; line-height: 36px; font-weight: 400;
    transform: scaleX(0.84); transform-origin: left top;
    text-shadow: 2px 3px 4px rgba(0,0,0,0.35);
  }
  .pitch-rule { position: absolute; left: 91px; width: 392px; height: 2px; background: var(--white); }
  .pitch-tick { position: absolute; left: 51px; width: 22px; height: 22px; }

  .portrait {
    position: absolute; left: 505px; top: 190px; width: 370px; height: 655px;
    background: linear-gradient(165deg, #cfc6bd 0%, #8d9bb3 30%, #3c5f9a 55%, #2a4a7e 100%);
    clip-path: polygon(95px 0, 265px 0, 300px 150px, 370px 320px, 370px 652px, 77px 493px, 6px 445px, 25px 290px, 110px 230px, 90px 120px);
  }
  .laptop-scene {
    position: absolute; left: 105px; top: 506px; width: 332px; height: 186px;
    background: linear-gradient(135deg, #f7b21c, #f07f1d);
    border: 5px solid var(--navy-dark); border-radius: 6px;
  }

  .remote {
    position: absolute; left: 58px; top: 724px; font-weight: 700; font-size: 66px;
    line-height: 59px; color: var(--navy-dark); white-space: nowrap;
    transform: scaleX(0.9); transform-origin: left top;
  }
  .divider { position: absolute; left: 312px; top: 733px; width: 5px; height: 110px; background: var(--navy-dark); }
  .count {
    position: absolute; left: 331px; top: 710px; font-family: "Montserrat", sans-serif;
    font-weight: 800; font-size: 116px; line-height: 116px; color: var(--navy-dark); letter-spacing: -3px;
    transform: scaleX(0.88); transform-origin: left top;
  }
  .count-label {
    position: absolute; left: 459px; top: 723px; font-weight: 700; font-size: 50px;
    line-height: 43px; color: var(--navy-dark); white-space: nowrap;
    transform: scaleX(0.9); transform-origin: left top;
  }
  .start-date {
    position: absolute; left: 337px; top: 815px; font-size: 31px; line-height: 31px; font-weight: 400;
    color: var(--navy-dark); white-space: nowrap;
  }
  .start-date span { color: var(--accent-blue); }

  .topics-tag { position: absolute; left: 58px; top: 932px; width: 186px; height: 82px; }
  .topics-tag svg { position: absolute; inset: 0; }
  .topics-tag p {
    position: absolute; left: 0; top: 10px; width: 172px; text-align: center; white-space: nowrap;
    font-size: 30px; line-height: 30px; color: var(--navy-dark); font-weight: 400;
    transform: scaleX(0.86); transform-origin: center top;
  }
  .topics { position: absolute; top: 896px; list-style: none; }
  .topics li {
    position: relative; padding-left: 30px; height: 33px; font-size: 17px; line-height: 24px;
    font-weight: 300; color: var(--topic-ink); white-space: nowrap;
  }
  .topics .tick { position: absolute; left: 0; top: 3px; width: 18px; height: 18px; }
  .topics.col-a { left: 262px; }
  .topics.col-b { left: 465px; }
  .topics.col-c { left: 670px; }

  .footer { position: absolute; left: 0; top: 1073px; width: 875px; height: 127px; background: var(--footer-grey); }
  .footer-shape { position: absolute; left: 0; top: 0; }
  .brand {
    position: absolute; left: 50px; top: 52px; font-size: 19px; font-weight: 500; color: var(--white);
  }
  .contact-call { position: absolute; left: 137px; top: 30px; color: var(--white); white-space: nowrap; }
  .contact-call .lead { font-size: 26px; line-height: 32px; font-weight: 300; }
  .contact-call .number { font-size: 30px; line-height: 34px; font-weight: 700; }
  .contact-list { position: absolute; left: 442px; top: 38px; color: var(--navy-dark); font-size: 19px; font-weight: 300; }
  .contact-list .item { position: absolute; white-space: nowrap; display: flex; align-items: center; gap: 10px; }
  .contact-list svg { width: 18px; height: 18px; flex: none; }
</style>
</head>
<body>
<main class="flyer">
  <svg class="backdrop" width="875" height="1200" viewBox="0 0 875 1200">
    <defs>
      <linearGradient id="studio" x1="0" y1="0" x2="1" y2="1">
        <stop offset="0" stop-color="#e8e8e8"/>
        <stop offset="1" stop-color="#cfcfcf"/>
      </linearGradient>
    </defs>
    <rect width="875" height="1200" fill="var(--paper)"/>
    <polygon points="540,175 875,98 875,850 582,683" fill="url(#studio)"/>
    <polygon points="0,690 424,585 875,850 875,1200 0,1200" fill="var(--white)"/>
    <path d="M0,330 H452 V410 Q452,428 436,440 L318,500 L0,690 Z" fill="var(--navy-dark)"/>
    <path d="M0,0 H260 L530,160 Q540,166 540,178 V270 Q540,282 530,289 L262,485 Q244,497 226,485 L0,360 Z" fill="var(--navy-mid)"/>
  </svg>

  <h1 class="headline">REAL ESTATE<br>CAREER COURSE</h1>

  <div class="pitch">
    <svg class="pitch-tick" style="top:153px" viewBox="0 0 24 24" fill="none" stroke="#fff" stroke-width="2"><path d="M18 12v8H2V4h12"/><path d="M7 11l4 4 11-12"/></svg>
    <p class="pitch-line" style="top:144px">How to Make Money In Real Estate?</p>
    <div class="pitch-rule" style="top:194px"></div>
    <svg class="pitch-tick" style="top:214px" viewBox="0 0 24 24" fill="none" stroke="#fff" stroke-width="2"><path d="M18 12v8H2V4h12"/><path d="M7 11l4 4 11-12"/></svg>
    <p class="pitch-line" style="top:207px">For those who have started or</p>
    <p class="pitch-line" style="top:242px">would like to go into Real Estate.</p>
    <div class="pitch-rule" style="top:293px"></div>
    <svg class="pitch-tick" style="top:316px" viewBox="0 0 24 24" fill="none" stroke="#fff" stroke-width="2"><path d="M18 12v8H2V4h12"/><path d="M7 11l4 4 11-12"/></svg>
    <p class="pitch-line" style="top:305px">An investment in knowledge</p>
    <p class="pitch-line" style="top:340px">opens up untold opportunities.</p>
  </div>

  <div class="portrait" role="img" aria-label="Photo of a smiling young man with short hair and beard in a blue suit, white shirt and dark tie"></div>
  <div class="laptop-scene" role="img" aria-label="Illustration of a laptop showing an online real estate lesson with houses, charts and an instructor, with a student watching on his own laptop"></div>

  <div class="remote">REMOTE<br>SESSIONS</div>
  <div class="divider"></div>
  <div class="count">12</div>
  <div class="count-label">session<br>course</div>
  <div class="start-date">Classes starting <span>June 16</span></div>

  <div class="topics-tag">
    <svg width="186" height="82" viewBox="0 0 186 82" fill="none" stroke="var(--navy-mid)" stroke-width="2"><path d="M1 1H168L184 41L168 81H1Z"/></svg>
    <p>A partial listing<br>of Topics</p>
  </div>

  <ul class="topics col-a">
    <li><svg class="tick" viewBox="0 0 24 24" fill="none" stroke="#2f5c9c" stroke-width="2"><path d="M18 12v8H2V4h12"/><path d="M7 11l4 4 11-12"/></svg>Single-family</li>
    <li><svg class="tick" viewBox="0 0 24 24" fill="none" stroke="#2f5c9c" stroke-width="2"><path d="M18 12v8H2V4h12"/><path d="M7 11l4 4 11-12"/></svg>Multifamily</li>
    <li><svg class="tick" viewBox="0 0 24 24" fill="none" stroke="#2f5c9c" stroke-width="2"><path d="M18 12v8H2V4h12"/><path d="M7 11l4 4 11-12"/></svg>Management</li>
    <li><svg class="tick" viewBox="0 0 24 24" fill="none" stroke="#2f5c9c" stroke-width="2"><path d="M18 12v8H2V4h12"/><path d="M7 11l4 4 11-12"/></svg>Real Estate Concepts</li>
    <li><svg class="tick" viewBox="0 0 24 24" fill="none" stroke="#2f5c9c" stroke-width="2"><path d="M18 12v8H2V4h12"/><path d="M7 11l4 4 11-12"/></svg>Real Estate law</li>
  </ul>
  <ul class="topics col-b">
    <li><svg class="tick" viewBox="0 0 24 24" fill="none" stroke="#2f5c9c" stroke-width="2"><path d="M18 12v8H2V4h12"/><path d="M7 11l4 4 11-12"/></svg>Investment properties</li>
    <li><svg class="tick" viewBox="0 0 24 24" fill="none" stroke="#2f5c9c" stroke-width="2"><path d="M18 12v8H2V4h12"/><path d="M7 11l4 4 11-12"/></svg>Foreclosures</li>
    <li><svg class="tick" viewBox="0 0 24 24" fill="none" stroke="#2f5c9c" stroke-width="2"><path d="M18 12v8H2V4h12"/><path d="M7 11l4 4 11-12"/></svg>Rehab</li>
    <li><svg class="tick" viewBox="0 0 24 24" fill="none" stroke="#2f5c9c" stroke-width="2"><path d="M18 12v8H2V4h12"/><path d="M7 11l4 4 11-12"/></svg>Foreclosures</li>
    <li><svg class="tick" viewBox="0 0 24 24" fill="none" stroke="#2f5c9c" stroke-width="2"><path d="M18 12v8H2V4h12"/><path d="M7 11l4 4 11-12"/></svg>Short sales</li>
  </ul>
  <ul class="topics col-c">
    <li><svg class="tick" viewBox="0 0 24 24" fill="none" stroke="#2f5c9c" stroke-width="2"><path d="M18 12v8H2V4h12"/><path d="M7 11l4 4 11-12"/></svg>Development</li>
    <li><svg class="tick" viewBox="0 0 24 24" fill="none" stroke="#2f5c9c" stroke-width="2"><path d="M18 12v8H2V4h12"/><path d="M7 11l4 4 11-12"/></svg>Finical modeling</li>
    <li><svg class="tick" viewBox="0 0 24 24" fill="none" stroke="#2f5c9c" stroke-width="2"><path d="M18 12v8H2V4h12"/><path d="M7 11l4 4 11-12"/></svg>HUD properties</li>
    <li><svg class="tick" viewBox="0 0 24 24" fill="none" stroke="#2f5c9c" stroke-width="2"><path d="M18 12v8H2V4h12"/><path d="M7 11l4 4 11-12"/></svg>Due Diligence</li>
  </ul>

  <footer class="footer">
    <svg class="footer-shape" width="460" height="127" viewBox="0 0 460 127">
      <path d="M0,10 H300 Q325,10 343,28 L455,127 H0 Z" fill="var(--navy-dark)"/>
    </svg>
    <div class="brand">Keystone</div>
    <div class="contact-call">
      <div class="lead">Contact Us Today</div>
      <div class="number">00198765432</div>
    </div>
    <div class="contact-list">
      <div class="item" style="left:0;top:0"><svg viewBox="0 0 24 24" fill="var(--navy-dark)"><path d="M3 9c0-3 4-5 9-5s9 2 9 5l-4 1-1-3c-2-1-6-1-8 0l-1 3z"/><path d="M6 12h12l2 8H4z"/><circle cx="12" cy="16" r="2" fill="#dcdcdc"/></svg>000 . 5550 . 1942</div>
      <div class="item" style="left:183px;top:0"><svg viewBox="0 0 24 24" fill="var(--navy-dark)"><path d="M2 6h20v12H2z"/><path d="M2 6l10 7 10-7" fill="none" stroke="#dcdcdc" stroke-width="1.5"/></svg>hello@keystonerealtyschool.com</div>
      <div class="item" style="left:0;top:32px"><svg viewBox="0 0 24 24" fill="var(--navy-dark)"><path d="M12 2a7 7 0 0 0-7 7c0 5 7 13 7 13s7-8 7-13a7 7 0 0 0-7-7z"/><circle cx="12" cy="9" r="2.6" fill="#dcdcdc"/></svg>2275 Larchmere Lane Fairhaven, WI 54000</div>
    </div>
  </footer>
</main>
</body>
</html>
```